Yard sign design for high end luxury home builder.

Need a design for signage on custom homes that are being built. I already have a logo that I am satisfied with that needs to be incorporated. I need the following incorporated in the design of the sign-
- Lic number 381526
- phone number (805) 555-0148‬
- quennbuilderscrew.com
- Logo/Branding

If possible it may be nice to have the following quote that is on are business cards-

Quote from Gerard of Norvelle-
HE WHO WORKS WITH HIS HANDS IS A LABORER.
HE WHO WORKS WITH HIS HANDS & HIS HEAD IS A CRAFTSMAN.
HE WHO WORKS WITH HIS HANDS & HIS HEAD & HIS HEART IS AN ARTISAN.
-GERARD OF NORVELLE

Target Market(s)

Archetect, Designers, Clients desiring to build a new home or remodel.

Colors
fde9d4
fee4d5
fabb94
fac994
faa54b
f68d4d
f37122
f78f20
f68e4e

Requirements
Must have
• - Lic number 381526
• - phone number (805) 555-0148‬
• - quennbuilderscrew.com
• - Logo/Branding
Nice to have
• Quote from Gerard of Norvelle-
• HE WHO WORKS WITH HIS HANDS IS A LABORER.
• HE WHO WORKS WITH HIS HANDS & HIS HEAD IS A CRAFTSMAN.
• HE WHO WORKS WITH HIS HANDS & HIS HEAD & HIS HEART IS AN ARTISAN.
• -GERARD OF NORVELLE
• OR the below statement-
• Craftsmen that Care
Should not have
• Any additional verbiage not specified above including any type of verbiage about what kind of company we are. For instance- Integrity, reputable... It's just all played out. Im just looking for a bitching design that has the info that compliments my logo/branding.

```html
<!DOCTYPE html>
<html lang="en">
<head>
<meta charset="utf-8">
<title>Quenn Builders Crew – Yard Sign</title>
<link rel="stylesheet" href="https://fonts.googleapis.com/css2?family=Crimson+Pro:wght@400;600;700&display=swap">
<style>
  :root {
    --page: #ffffff;
    --dark-panel: #191615;
    --light-panel: #eef0ef;
    --tan: #a48c72;
    --brown: #4a3020;
    --cream: #f2ece4;
  }
  * { margin: 0; padding: 0; box-sizing: border-box; }
  html, body { width: 1200px; height: 1200px; overflow: hidden; background: var(--page); }
  body { position: relative; font-family: "Crimson Pro", Georgia, serif; }

  .sign {
    position: absolute;
    top: 246px;
    width: 523px;
    height: 696px;
    --ink: var(--tan);
    --tab-text: var(--dark-panel);
  }
  .sign--dark { left: 58px; background: var(--dark-panel); --ink: var(--tan); --tab-text: #1c1715; }
  .sign--light { left: 611px; background: var(--light-panel); --ink: var(--brown); --tab-text: var(--cream); }

  .sign__frame {
    position: absolute; inset: 8px;
    border: 1.5px solid var(--ink);
  }
  .sign__phone {
    position: absolute; top: 22px; left: 0; right: 0;
    text-align: center; color: var(--ink);
    font-size: 64px; font-weight: 400; letter-spacing: 1px;
    font-variant-numeric: oldstyle-nums;
  }
  .brand {
    position: absolute; top: 150px; left: 0; right: 0; height: 300px;
    display: flex; flex-direction: column; align-items: center; justify-content: center;
    color: var(--ink); font-weight: 700; text-transform: uppercase; line-height: 1;
  }
  .brand__square { width: 150px; height: 150px; background: var(--ink); margin-bottom: 26px; }
  .brand__name { font-size: 58px; letter-spacing: 4px; }
  .brand__sub { font-size: 25px; letter-spacing: 3px; margin-top: 6px; }

  .sign__tagline {
    position: absolute; top: 474px; left: 0; right: 0;
    text-align: center; color: var(--ink); font-size: 45px; font-weight: 400;
  }
  .quote {
    position: absolute; top: 536px; left: 0; right: 0;
    text-align: center; color: var(--ink);
  }
  .quote__text { font-size: 14.5px; line-height: 15px; }
  .quote__mark { position: absolute; font-size: 34px; line-height: 1; font-weight: 600; }
  .quote__mark--open { left: 58px; top: -6px; }
  .quote__mark--close { left: 440px; top: 44px; }
  .quote__rule {
    width: 178px; height: 1px; background: var(--ink);
    margin: 11px auto 0;
  }
  .quote__author { font-size: 13px; font-weight: 700; margin-top: 4px; }

  .sign__web {
    position: absolute; left: 95px; top: 646px; width: 333px; height: 42px;
    background: var(--ink); border-radius: 16px 16px 0 0;
    color: var(--tab-text); font-size: 26px; text-align: center; line-height: 40px;
  }
  .sign__license {
    position: absolute; left: 478px; top: 667px;
    color: var(--ink); font-size: 9.5px; font-weight: 600;
  }
</style>
</head>
<body>

  <section class="sign sign--dark">
    <div class="sign__frame"></div>
    <p class="sign__phone">(805) 555 0148</p>
    <div class="brand">
      <div class="brand__square"></div>
      <span class="brand__name">Quenn</span>
      <span class="brand__sub">Builders Crew Inc.</span>
    </div>
    <p class="sign__tagline">Craftsmen That Care</p>
    <div class="quote">
      <span class="quote__mark quote__mark--open">“</span>
      <p class="quote__text">He who works with his hands is a laborer.<br>He who works with his hands &amp; his head is a craftsman.<br>He who works with his hands &amp; his head &amp; his heart is<br>an artisan.</p>
      <span class="quote__mark quote__mark--close">”</span>
      <div class="quote__rule"></div>
      <p class="quote__author">Gerard of Norvelle</p>
    </div>
    <p class="sign__web">quennbuilderscrew.com</p>
    <p class="sign__license">Lic 381526</p>
  </section>

  <section class="sign sign--light">
    <div class="sign__frame"></div>
    <p class="sign__phone">(805) 555 0148</p>
    <div class="brand">
      <div class="brand__square"></div>
      <span class="brand__name">Quenn</span>
      <span class="brand__sub">Builders Crew Inc.</span>
    </div>
    <p class="sign__tagline">Craftsmen That Care</p>
    <div class="quote">
      <span class="quote__mark quote__mark--open">“</span>
      <p class="quote__text">He who works with his hands is a laborer.<br>He who works with his hands &amp; his head is a craftsman.<br>He who works with his hands &amp; his head &amp; his heart is<br>an artisan.</p>
      <span class="quote__mark quote__mark--close">”</span>
      <div class="quote__rule"></div>
      <p class="quote__author">Gerard of Norvelle</p>
    </div>
    <p class="sign__web">quennbuilderscrew.com</p>
    <p class="sign__license">Lic 381526</p>
  </section>

</body>
</html>
```